Oil and Gas Exploration and Production company needs a business card design

We need a business card design using our logo and colors in the logo. We want a mainstream design.

```html
<!DOCTYPE html>
<html lang="en">
<head>
<meta charset="utf-8">
<title>Corvan Oil &amp; Gas – Business Card</title>
<link rel="stylesheet" href="https://fonts.googleapis.com/css2?family=Lato:wght@400;700;900&display=swap">
<style>
  :root {
    --page-bg: #e4e5e7;
    --card-light: #f7f7f6;
    --card-dark: #141414;
    --card-dark-2: #2a2a2a;
    --gold: #b8862b;
    --gold-light: #d9a64a;
    --ink: #111111;
    --muted: #d6d6d6;
    --contact-text: #f1f1f1;
  }
  html, body {
    margin: 0;
    padding: 0;
    width: 1200px;
    height: 970px;
    overflow: hidden;
    background: var(--page-bg);
    font-family: "Lato", Arial, sans-serif;
  }
  .canvas {
    position: relative;
    width: 1200px;
    height: 970px;
  }
  .business-card {
    position: absolute;
    left: 100px;
    top: 185px;
    width: 1000px;
    height: 600px;
    background: var(--card-light);
    box-shadow: 0 14px 40px rgba(0,0,0,0.18);
    overflow: hidden;
  }
  .card-shapes {
    position: absolute;
    inset: 0;
    width: 1000px;
    height: 600px;
  }
  .brand {
    position: absolute;
    left: 0;
    right: 0;
    top: 130px;
    display: flex;
    align-items: center;
    justify-content: center;
    gap: 22px;
  }
  .brand-dot {
    width: 52px;
    height: 52px;
    border-radius: 50%;
    background: var(--gold);
  }
  .brand-name {
    font-weight: 900;
    font-size: 74px;
    line-height: 1;
    color: var(--ink);
    letter-spacing: -0.5px;
  }
  .holder {
    position: absolute;
    right: 572px;
    top: 452px;
    text-align: right;
  }
  .holder-name {
    font-weight: 700;
    font-size: 24px;
    color: var(--gold-light);
    letter-spacing: 0.5px;
    text-transform: uppercase;
  }
  .holder-role {
    margin-top: 6px;
    font-size: 20px;
    color: var(--muted);
  }
  .contact-list {
    position: absolute;
    left: 511px;
    top: 424px;
    margin: 0;
    padding: 0;
    list-style: none;
  }
  .contact-item {
    display: flex;
    align-items: center;
    height: 38px;
    font-size: 21px;
    color: var(--contact-text);
    letter-spacing: 0.3px;
  }
  .contact-item svg {
    width: 26px;
    height: 26px;
    margin-right: 20px;
    flex: none;
  }
  .contact-web {
    font-weight: 700;
    color: var(--gold-light);
  }
</style>
</head>
<body>
<main class="canvas">
  <section class="business-card">
    <svg class="card-shapes" viewBox="0 0 1000 600" aria-hidden="true">
      <defs>
        <linearGradient id="dark-band" x1="0" y1="0" x2="1" y2="0">
          <stop offset="0" stop-color="var(--card-dark-2)"/>
          <stop offset="0.5" stop-color="var(--card-dark)"/>
          <stop offset="1" stop-color="var(--card-dark-2)"/>
        </linearGradient>
        <linearGradient id="gold-swoosh" x1="0" y1="0" x2="1" y2="0">
          <stop offset="0" stop-color="#8a5e17"/>
          <stop offset="0.5" stop-color="#d4a14a"/>
          <stop offset="1" stop-color="#8a5e17"/>
        </linearGradient>
        <linearGradient id="divider-fade" x1="0" y1="0" x2="0" y2="1">
          <stop offset="0" stop-color="#c9953a" stop-opacity="0"/>
          <stop offset="0.5" stop-color="#c9953a" stop-opacity="1"/>
          <stop offset="1" stop-color="#c9953a" stop-opacity="0"/>
        </linearGradient>
      </defs>
      <path class="swoosh" d="M60 432 Q503 214 947 440 Q503 236 60 432 Z" fill="url(#gold-swoosh)"/>
      <path class="dark-band" d="M0 468 Q503 250 1000 475 L1000 600 L0 600 Z" fill="url(#dark-band)"/>
      <rect class="divider" x="478" y="410" width="2" height="152" fill="url(#divider-fade)"/>
    </svg>

    <div class="brand">
      <span class="brand-dot"></span>
      <span class="brand-name">Corvan Oil &amp; Gas</span>
    </div>

    <div class="holder">
      <div class="holder-name">Daniel Harper</div>
      <div class="holder-role">General Manager</div>
    </div>

    <ul class="contact-list">
      <li class="contact-item">
        <svg viewBox="0 0 26 26" aria-hidden="true">
          <circle cx="13" cy="13" r="12" fill="var(--gold)"/>
          <path d="M8 10.5c0-1.5 2.2-2.5 5-2.5s5 1 5 2.5v1h-2.4v-1.2h-5.2v1.2H8z M9.5 12.5h7l1.5 5.5H8z" fill="#1a1a1a"/>
        </svg>
        0161 555 0182
      </li>
      <li class="contact-item">
        <svg viewBox="0 0 26 26" aria-hidden="true">
          <circle cx="13" cy="13" r="12" fill="var(--gold)"/>
          <rect x="9.5" y="6.5" width="7" height="13" rx="1.4" fill="none" stroke="#1a1a1a" stroke-width="1.6"/>
          <circle cx="13" cy="17" r="0.9" fill="#1a1a1a"/>
        </svg>
        dharper@corvan-energy.co.uk
      </li>
      <li class="contact-item contact-web">
        <svg viewBox="0 0 26 26" aria-hidden="true">
          <circle cx="13" cy="13" r="12" fill="var(--gold)"/>
          <rect x="7.5" y="9" width="11" height="8" fill="none" stroke="#1a1a1a" stroke-width="1.5"/>
          <path d="M7.5 9 L13 13.5 L18.5 9" fill="none" stroke="#1a1a1a" stroke-width="1.5"/>
        </svg>
        www.corvan-energy.co.uk
      </li>
    </ul>
  </section>
</main>
</body>
</html>
```